Pharmacy ad

need 2 pharmacy ads for the phone book. one for Brookvale Pharmacy and one for Cedarline Care Pharmacy. Dimensions for ad is 4.75in x 4.667 in. please see attached examples of ad uploaded as well logos of each pharmacy

```html
<!DOCTYPE html>
<html lang="en">
<head>
<meta charset="utf-8">
<title>Cedarline Care Pharmacy – Directory Ad</title>
<link href="https://fonts.googleapis.com/css2?family=Montserrat:wght@400;500;600;700;800&family=Exo+2:ital,wght@1,600&display=swap" rel="stylesheet">
<style>
  :root {
    --brand-blue: #3b53a4;
    --brand-green: #6cbd45;
    --paper: #ffffff;
    --photo-light: #e9eef0;
    --photo-mid: #c9d6da;
  }
  * { box-sizing: border-box; margin: 0; padding: 0; }
  html, body { width: 1200px; height: 1200px; overflow: hidden; background: var(--paper); }
  body { font-family: "Montserrat", Arial, sans-serif; color: var(--brand-blue); position: relative; }

  .ad { position: absolute; inset: 0; }

  /* Header */
  .brand { position: absolute; left: 62px; top: 110px; display: flex; align-items: center; gap: 22px; }
  .brand-dot { width: 46px; height: 46px; border-radius: 50%; background: var(--brand-green); }
  .brand-name { font-size: 58px; font-weight: 700; line-height: 1; color: var(--brand-blue); letter-spacing: -0.5px; white-space: nowrap; }

  .hours { position: absolute; right: 68px; top: 92px; text-align: right; font-weight: 600; font-size: 24px; line-height: 31px; }
  .hours-title { font-weight: 800; font-size: 21px; }

  .tagline { position: absolute; right: 65px; top: 258px; font-family: "Exo 2", Arial, sans-serif; font-style: italic; font-weight: 600; font-size: 41px; color: var(--brand-green); }

  /* Photo + services */
  .photo { position: absolute; left: 0; top: 262px; width: 640px; height: 456px;
    background: linear-gradient(120deg, var(--photo-light) 0%, var(--photo-mid) 55%, #dfe7ea 100%); }
  .services-panel { position: absolute; left: 0; top: 0; }

  .services { position: absolute; left: 640px; top: 350px; list-style: none; font-weight: 600; font-size: 28px; line-height: 36px; color: var(--paper); }
  .services li { position: relative; padding-left: 46px; margin-bottom: 10px; }
  .services svg { position: absolute; left: 0; top: 4px; }

  /* Discounts */
  .discount-band { position: absolute; left: 0; top: 718px; width: 1200px; height: 202px; background: var(--brand-green); }
  .discount { position: absolute; top: 733px; height: 177px; background: var(--paper); border-radius: 22px 0 40px 0; display: flex; align-items: center; }
  .discount-senior { left: 65px; width: 518px; }
  .discount-student { left: 620px; width: 518px; }
  .discount-figure { font-weight: 800; font-size: 136px; letter-spacing: -8px; line-height: 1; }
  .discount-senior .discount-figure { margin-left: 12px; margin-top: 8px; }
  .discount-student .discount-figure { margin-left: 18px; margin-top: -30px; }
  .discount-label { font-weight: 800; font-size: 33px; line-height: 38px; margin-left: 18px; }
  .discount-student .discount-label { margin-top: -40px; }
  .discount-note { position: absolute; left: 160px; bottom: 6px; font-size: 24px; font-weight: 400; }

  /* Services bar */
  .services-bar { position: absolute; left: 0; top: 920px; }
  .services-bar-text { position: absolute; left: 63px; top: 930px; color: var(--paper); font-weight: 700; font-size: 35px; white-space: nowrap; }

  /* Contacts */
  .contacts { position: absolute; left: 63px; top: 990px; font-weight: 600; font-size: 25px; line-height: 40px; list-style: none; }
  .contacts li { position: relative; padding-left: 40px; white-space: nowrap; }
  .contacts .phone { font-size: 31px; }
  .contacts .email { font-size: 30px; }
  .contacts svg { position: absolute; left: 0; top: 6px; }

  .social { position: absolute; left: 583px; top: 1062px; display: flex; align-items: center; gap: 14px; }
  .social-square { width: 58px; height: 58px; background: var(--brand-blue); }
  .social-text { line-height: 1; }
  .social-lead { font-weight: 700; font-size: 22px; }
  .social-name { font-weight: 700; font-size: 29px; margin-top: 3px; white-space: nowrap; }

  .accept { position: absolute; left: 838px; top: 960px; width: 315px; text-align: center; }
  .accept-title { font-weight: 500; font-size: 24px; letter-spacing: 8px; }
  .insurer { margin-top: 14px; display: flex; align-items: center; justify-content: center; gap: 10px; font-weight: 700; font-size: 24px; white-space: nowrap; }
  .insurer-dot { width: 24px; height: 24px; border-radius: 50%; background: var(--brand-green); }

  .cards { position: absolute; left: 852px; top: 1080px; width: 290px; display: flex; justify-content: space-between; align-items: center; font-weight: 700; font-size: 15px; white-space: nowrap; }
  .card { display: flex; align-items: center; gap: 4px; }
  .card-dot { width: 12px; height: 12px; border-radius: 50%; background: var(--brand-green); }
</style>
</head>
<body>
<main class="ad">

  <header>
    <div class="brand">
      <span class="brand-dot"></span>
      <span class="brand-name">Cedarline Care Pharmacy</span>
    </div>
    <div class="hours">
      <div class="hours-title">OPENING HOURS:</div>
      <div>Mon - Sat</div>
      <div>8:30am - 7pm</div>
      <div>Sun - 10am-2pm</div>
    </div>
  </header>

  <div class="photo" role="img" aria-label="Photo of a smiling pharmacist in a white coat helping a customer at the pharmacy counter, shelves behind"></div>

  <svg class="services-panel" width="1200" height="720" viewBox="0 0 1200 720" aria-hidden="true">
    <polygon points="622,312 1200,312 1200,718 507,718" fill="#3b53a4"/>
  </svg>

  <p class="tagline">Where good health begins</p>

  <ul class="services">
    <li><svg width="32" height="30" viewBox="0 0 32 30"><path d="M3 16 L12 25 L29 3" fill="none" stroke="#6cbd45" stroke-width="5" stroke-linecap="round" stroke-linejoin="round"/></svg>Certified Pharmacists</li>
    <li><svg width="32" height="30" viewBox="0 0 32 30"><path d="M3 16 L12 25 L29 3" fill="none" stroke="#6cbd45" stroke-width="5" stroke-linecap="round" stroke-linejoin="round"/></svg>Affordable prices</li>
    <li><svg width="32" height="30" viewBox="0 0 32 30"><path d="M3 16 L12 25 L29 3" fill="none" stroke="#6cbd45" stroke-width="5" stroke-linecap="round" stroke-linejoin="round"/></svg>Brand and Generic Medicines</li>
    <li><svg width="32" height="30" viewBox="0 0 32 30"><path d="M3 16 L12 25 L29 3" fill="none" stroke="#6cbd45" stroke-width="5" stroke-linecap="round" stroke-linejoin="round"/></svg>Blood Pressure and<br>Glucose checks</li>
    <li><svg width="32" height="30" viewBox="0 0 32 30"><path d="M3 16 L12 25 L29 3" fill="none" stroke="#6cbd45" stroke-width="5" stroke-linecap="round" stroke-linejoin="round"/></svg>Personal care and Beauty<br>Products</li>
    <li><svg width="32" height="30" viewBox="0 0 32 30"><path d="M3 16 L12 25 L29 3" fill="none" stroke="#6cbd45" stroke-width="5" stroke-linecap="round" stroke-linejoin="round"/></svg>Injectables</li>
  </ul>

  <section>
    <div class="discount-band"></div>
    <div class="discount discount-senior">
      <span class="discount-figure">10%</span>
      <span class="discount-label">SENIOR<br>CITIZEN<br>DISCOUNT</span>
    </div>
    <div class="discount discount-student">
      <span class="discount-figure">10%</span>
      <span class="discount-label">STUDENT<br>DISCOUNT</span>
      <span class="discount-note">With valid ID card</span>
    </div>
  </section>

  <svg class="services-bar" width="820" height="62" viewBox="0 0 820 62" aria-hidden="true">
    <polygon points="0,0 820,0 804,62 0,62" fill="#3b53a4"/>
  </svg>
  <p class="services-bar-text">SPECIAL ORDERS | DELIVERY SERVICE</p>

  <ul class="contacts">
    <li><svg width="30" height="30" viewBox="0 0 30 30"><circle cx="15" cy="15" r="13" fill="none" stroke="#6cbd45" stroke-width="2"/><path d="M8 15 L15 8 L22 15 M10 14 V22 H20 V14" fill="none" stroke="#6cbd45" stroke-width="2.4"/></svg>Unit 4, Harbour View Plaza, Marine Road, Port Selwyn</li>
    <li class="phone"><svg width="30" height="30" viewBox="0 0 30 30"><circle cx="15" cy="15" r="13" fill="none" stroke="#6cbd45" stroke-width="2"/><path d="M10 8 L13 8 L14 12 L12 13.5 Q14 17 16.5 18 L18 16 L22 17 L22 20 Q15 22 10 14 Z" fill="#6cbd45"/></svg>1 555 318 2046 / 1 555 318 2047<br>1 555 318 2048</li>
    <li class="email"><svg width="30" height="30" viewBox="0 0 30 30"><circle cx="15" cy="15" r="13" fill="none" stroke="#6cbd45" stroke-width="2"/><rect x="8" y="10" width="14" height="10" fill="none" stroke="#6cbd45" stroke-width="2"/><path d="M8 10 L15 16 L22 10" fill="none" stroke="#6cbd45" stroke-width="2"/></svg>cedarlinecare@example.com</li>
  </ul>

  <div class="social">
    <span class="social-square"></span>
    <div class="social-text">
      <div class="social-lead">Visit us on:</div>
      <div class="social-name">Chatterbook</div>
    </div>
  </div>

  <div class="accept">
    <div class="accept-title">WE ACCEPT</div>
    <div class="insurer"><span class="insurer-dot"></span>Harborline Insurance</div>
  </div>
  <div class="cards">
    <span class="card"><span class="card-dot"></span>Sunwave</span>
    <span class="card"><span class="card-dot"></span>CirclePay</span>
    <span class="card"><span class="card-dot"></span>TrustCard</span>
  </div>

</main>
</body>
</html>
```